Business Card for Industrial Distributor

We need a business card design for an industrial distributor. We sell machine parts for the manufacturing and oil industry. We would like the cards to look clean and modern but with a touch of industry.

Our colors are blue/white.

Please feel free to visit our website www.korvelpartsco.com

Target Market(s)

mexican manufacturers in the automobile/aerospace industry

Industry/Entity Type

Industrial

Colors
ffffff
0555a3

```html
<!DOCTYPE html>
<html lang="en">
<head>
<meta charset="utf-8">
<title>Korvel Business Card</title>
<link href="https://fonts.googleapis.com/css2?family=Open+Sans:wght@400;600;700;800&display=swap" rel="stylesheet">
<style>
  :root {
    --page-bg: #ececec;
    --card-dark: #060606;
    --card-dark-panel: #1b1b1d;
    --card-light: #ffffff;
    --text-light: #ffffff;
    --text-muted: #e6e6e6;
    --brand-bright: #3d5cf2;
    --brand-navy: #25338c;
    --brand-blue: #0555a3;
  }
  * { margin: 0; padding: 0; box-sizing: border-box; }
  html, body {
    width: 1200px; height: 900px; overflow: hidden;
    background: var(--page-bg);
    font-family: "Open Sans", Arial, sans-serif;
  }
  .stage { position: relative; width: 1200px; height: 900px; }
  .card { position: absolute; overflow: hidden; box-shadow: 0 6px 18px rgba(0,0,0,0.18); }

  /* Front (dark) */
  .card-front {
    left: 238px; top: 62px; width: 555px; height: 343px;
    background: var(--card-dark); color: var(--text-light);
  }
  .card-front .panel {
    position: absolute; inset: 0;
    background: var(--card-dark-panel);
    clip-path: polygon(445px 0, 555px 0, 555px 343px, 220px 343px);
  }
  .holder { position: absolute; left: 36px; top: 30px; }
  .holder-name { font-size: 18px; font-weight: 700; line-height: 22px; }
  .holder-role { font-size: 16px; font-weight: 400; line-height: 22px; color: var(--text-muted); }
  .front-wordmark {
    position: absolute; left: 36px; top: 100px;
    font-size: 50px; font-weight: 800; line-height: 70px;
    color: var(--brand-bright); letter-spacing: 0.5px;
  }
  .contact-list { position: absolute; left: 35px; list-style: none; font-size: 16px; line-height: 21px; }
  .contact-list.phones { top: 204px; }
  .contact-list.online { top: 267px; }
  .contact-list li { display: flex; align-items: center; gap: 5px; }
  .contact-list svg { width: 11px; height: 11px; fill: var(--text-light); flex: none; }
  .address {
    position: absolute; right: 30px; top: 269px;
    text-align: right; font-size: 15px; line-height: 22px; font-style: normal;
  }

  /* Back (white) */
  .card-back {
    left: 458px; top: 518px; width: 560px; height: 343px;
    background: var(--card-light);
  }
  .back-logo {
    position: absolute; left: 72px; top: 138px;
    display: flex; align-items: center; gap: 20px;
  }
  .back-logo .dot { width: 66px; height: 66px; border-radius: 50%; background: var(--brand-blue); }
  .back-wordmark { font-size: 58px; font-weight: 800; color: var(--brand-navy); line-height: 66px; }
</style>
</head>
<body>
<main class="stage">
  <section class="card card-front">
    <div class="panel"></div>
    <div class="holder">
      <p class="holder-name">Daniel Marsh</p>
      <p class="holder-role">Owner</p>
    </div>
    <p class="front-wordmark">Korvel</p>
    <ul class="contact-list phones">
      <li><svg viewBox="0 0 12 12"><path d="M1 4c0-2 2-3 5-3s5 1 5 3v1H8V4H4v1H1zM3 6h6l2 4v1H1v-1z"/></svg>312-555-0148</li>
      <li><svg viewBox="0 0 12 12"><path d="M3 0h6v12H3zM4 1.5v7.5h4V1.5z"/></svg>312-555-01927</li>
    </ul>
    <ul class="contact-list online">
      <li><svg viewBox="0 0 12 12"><path d="M0 2h12v1L6 7 0 3zM0 4.5l6 4 6-4V10H0z"/></svg>info@yourname.com</li>
      <li><svg viewBox="0 0 12 12"><circle cx="6" cy="6" r="6"/></svg>www.website.com</li>
    </ul>
    <address class="address">240 W. Harlan Suite 810<br>Chicago, Illinois 60610</address>
  </section>

  <section class="card card-back">
    <div class="back-logo">
      <span class="dot"></span>
      <span class="back-wordmark">Korvel</span>
    </div>
  </section>
</main>
</body>
</html>
```